Gobal construction supply company needs new business card design

I need a business card design for my global supply company using an existing logo. i will be looking to print these on rounded corner cards with the black background version of my logo on the back. on the front white background, my logo again and my simple details.

```html
<!DOCTYPE html>
<html lang="en">
<head>
<meta charset="utf-8">
<title>Southern Forge Supply – Business Card</title>
<link href="https://fonts.googleapis.com/css2?family=Lato:wght@400;700;900&display=swap" rel="stylesheet">
<style>
  :root {
    --stage: #2b2b2d;
    --card-white: #f3f4f6;
    --card-black: #1c1d1f;
    --ink: #1a1a1a;
    --ink-soft: #3a3a3a;
    --red: #d40f14;
    --rule: #9a9a9a;
    --rule-soft: #c8c8c8;
    --white: #ffffff;
  }
  * { margin: 0; padding: 0; box-sizing: border-box; }
  html, body {
    width: 1200px; height: 1108px; overflow: hidden;
    background: var(--stage);
    font-family: "Lato", sans-serif;
  }
  .stage {
    position: relative; width: 1200px; height: 1108px;
    display: flex; justify-content: center; align-items: center; gap: 80px;
  }
  .card {
    width: 400px; height: 700px; border-radius: 26px;
    position: relative; display: flex; flex-direction: column; align-items: center;
  }
  .card--front { background: var(--card-white); color: var(--ink); }
  .card--back { background: var(--card-black); color: var(--white); justify-content: center; }

  .brand {
    font-weight: 900; text-transform: uppercase; letter-spacing: 0.5px;
    text-align: center;
  }
  .card--front .brand { margin-top: 172px; font-size: 24px; color: var(--ink); }
  .card--back .brand { font-size: 34px; color: var(--white); line-height: 1.15; }

  .person { margin-top: 96px; text-align: center; }
  .person__name { color: var(--red); font-size: 27px; font-weight: 400; text-transform: uppercase; letter-spacing: 0.5px; }
  .person__title { font-size: 20px; color: var(--ink-soft); margin-top: 2px; }

  .icon-rule { display: flex; align-items: center; gap: 6px; width: 250px; margin-top: 16px; }
  .icon-rule::before, .icon-rule::after { content: ""; flex: 1; height: 1px; background: var(--rule); }
  .icon-rule svg { width: 20px; height: 20px; }

  .contact { text-align: center; font-size: 20px; line-height: 1.3; color: var(--ink); margin-top: 8px; }
  .divider { width: 230px; height: 1px; background: var(--rule-soft); margin: 12px 0; }
  .address { text-align: center; font-size: 20px; line-height: 1.3; color: var(--ink); }

  .card__web {
    position: absolute; bottom: 70px; left: 0; right: 0; text-align: center;
    color: var(--red); font-size: 20px; letter-spacing: 0.5px;
  }
</style>
</head>
<body>
<main class="stage">
  <section class="card card--front" aria-label="Card front">
    <p class="brand">Southern Forge Supply</p>

    <div class="person">
      <p class="person__name">Marcus Hale</p>
      <p class="person__title">Managing Director</p>
    </div>

    <div class="icon-rule">
      <svg viewBox="0 0 20 20" aria-label="Phone"><circle cx="10" cy="10" r="10" fill="var(--red)"/><path d="M6.5 5.5c.6-.6 1.4-.5 1.7.2l.7 1.5c.2.4 0 .9-.3 1.1l-.6.5c.6 1.3 1.6 2.3 2.9 2.9l.5-.6c.3-.3.7-.5 1.1-.3l1.5.7c.7.3.8 1.1.2 1.7l-.7.7c-3.6.2-7.9-4.1-7.7-7.7z" fill="#fff"/></svg>
      <svg viewBox="0 0 20 20" aria-label="Email"><circle cx="10" cy="10" r="10" fill="var(--red)"/><rect x="5" y="6.5" width="10" height="7" rx="1" fill="#fff"/><path d="M5.5 7l4.5 3.5L14.5 7" stroke="var(--red)" stroke-width="1" fill="none"/></svg>
      <svg viewBox="0 0 20 20" aria-label="Location"><circle cx="10" cy="10" r="10" fill="var(--red)"/><path d="M10 4.5a3.5 3.5 0 0 0-3.5 3.5c0 2.6 3.5 6.5 3.5 6.5s3.5-3.9 3.5-6.5A3.5 3.5 0 0 0 10 4.5z" fill="#fff"/><circle cx="10" cy="8" r="1.3" fill="var(--red)"/></svg>
    </div>

    <div class="contact">
      <p>410 727 3391</p>
      <p>hello@forgesupply.co</p>
      <p>www.forgesupply.co</p>
    </div>
    <div class="divider"></div>
    <div class="address">
      <p>88 Harbour Road, Unit 4,</p>
      <p>Port Kembla, 2505</p>
    </div>
  </section>

  <section class="card card--back" aria-label="Card back">
    <p class="brand">Southern Forge<br>Supply</p>
    <p class="card__web">WWW.FORGESUPPLY.CO</p>
  </section>
</main>
</body>
</html>
```